Revamp Website To A More Modern Up To Date Design Concepts

I am looking for a renewed look for my website.

Keep in mind that my business is B2B.

Please use and include all current content, text and imagery (you can adjust the imagery to fit your designs) and all current modules, features, videos, calls to action buttons, etc. Please do not omit anything from the current homepage. I prefer to see all my content as it is on my current site on the new design too so I can really invision my new site...so please do not use lipsum lorem text filler anywhere.

I am looking for an impressive looking and engaging high converting homepage.

Please be sure to keep all elements, links in header and footer etc. already on my current homepage at www.brightlanepromoworks.biz

Industry/Entity Type

marketing

Coding

Coded - Design and coding required

Number of Pages Required

3 page

Requirements
Must have
• impressive design
Nice to have
• im open
Should not have
• open

```html
<!DOCTYPE html>
<html lang="en">
<head>
<meta charset="utf-8">
<title>BrightLane Promo Works – Homepage Concept</title>
<link href="https://fonts.googleapis.com/css2?family=Montserrat:wght@500;600;700;800&family=Open+Sans:wght@400;600;700&display=swap" rel="stylesheet">
<style>
:root{
  --stage:#1d6cbf;
  --stage-dark:#175aa3;
  --blue:#1a6fc6;
  --blue-bright:#2a86e0;
  --navy:#1b1a72;
  --purple:#2e2ca8;
  --ink:#1c1c22;
  --text:#555a63;
  --muted:#8a8f98;
  --section-gray:#eeeff1;
  --nav:#4b4b4f;
  --line:#e1e3e7;
  --white:#ffffff;
}
*{margin:0;padding:0;box-sizing:border-box}
html,body{width:1200px;height:1086px;overflow:hidden;background:var(--stage)}
body{font-family:"Open Sans",sans-serif;color:var(--text)}
.stage{position:absolute;left:0;top:0;width:2016px;height:1825px;transform:scale(.5953);transform-origin:0 0;
  background:linear-gradient(90deg,var(--stage-dark),var(--stage) 20%,var(--stage) 80%,var(--stage-dark))}
.page{position:absolute;width:624px;background:var(--white);overflow:hidden}
.page-one{left:36px;top:36px;height:1789px}
.page-two{left:696px;top:0;height:1825px}
.page-three{left:1356px;top:0;height:1788px}
.a{position:absolute}
.h{font-family:"Montserrat",sans-serif;color:var(--ink);font-weight:700}
.btn{position:absolute;height:20px;border-radius:11px;background:var(--blue);color:#fff;font:700 7.6px/20px "Montserrat",sans-serif;text-align:center;box-shadow:0 2px 5px rgba(10,40,120,.25)}
.btn.light{background:#fff;color:var(--blue);border:1px solid var(--line);box-shadow:none}
.p{font-size:7.4px;line-height:11px;color:var(--text)}
.p b{color:var(--ink)}
.center{text-align:center}
.right{text-align:right}
.ph{position:absolute;border-radius:4px}
.wordmark{font:700 12px "Montserrat",sans-serif;color:var(--blue);letter-spacing:.2px}
.wordmark i{display:inline-block;width:13px;height:13px;background:var(--blue);border-radius:3px;vertical-align:-2px;margin-right:5px}
.topbar{left:0;top:0;width:624px;height:40px;background:#fff}
.navbar{left:0;top:40px;width:624px;height:22px;background:var(--nav)}
.navbar span{position:absolute;top:0;font:600 7px/22px "Open Sans",sans-serif;color:#eee}
.navbar .active{background:var(--blue);padding:0 6px;height:18px;top:2px;line-height:18px;border-radius:2px}
.pill{position:absolute;height:18px;border-radius:10px;font:700 7px/18px "Montserrat",sans-serif;text-align:center}
.social{position:absolute;width:16px;height:16px;border-radius:50%;background:#fff;border:1px solid #d5dbe6}
.social::after{content:"";position:absolute;left:5px;top:5px;width:5px;height:5px;border-radius:50%;background:var(--blue)}
.ticklist{list-style:none}
.ticklist li{position:relative;padding-left:13px;margin-bottom:7px}
.ticklist li::before{content:"";position:absolute;left:0;top:2px;width:7px;height:7px;border-radius:50%;background:var(--blue-bright)}
.ticklist .t{font:600 7.4px/10px "Open Sans",sans-serif;color:var(--blue)}
.ticklist .d{font-size:7px;line-height:10px;color:var(--text)}
.dotlist{list-style:none;font-size:7.4px;line-height:14.5px;color:#e6e8ff}
.dotlist li{position:relative;padding-left:9px}
.dotlist li::before{content:"";position:absolute;left:0;top:6px;width:3px;height:3px;border-radius:50%;background:#8fb8ff}
.bullets{list-style:none;font-size:7.2px;line-height:10.8px;color:#e3e5ff}
.bullets li{position:relative;padding-left:10px;margin-bottom:7px}
.bullets li::before{content:"";position:absolute;left:0;top:4px;width:3px;height:3px;border-radius:50%;background:#9cc2ff}
.stat{position:absolute;width:78px;text-align:center;font-size:6.6px;line-height:9px;color:var(--muted)}
.stat b{display:block;font:700 8px/11px "Montserrat",sans-serif;color:var(--ink)}
.icon{position:absolute;width:16px;height:16px;border:1.5px solid var(--blue);border-radius:3px}
.icon::after{content:"";position:absolute;left:3px;right:3px;top:5px;height:1.5px;background:var(--blue);box-shadow:0 3px 0 var(--blue)}
.ficon{position:absolute;width:18px;height:18px;border:1.4px solid #666c78;border-radius:50%}
.feature-title{font:700 7.4px/10px "Montserrat",sans-serif;color:var(--ink)}
.divider{position:absolute;height:1px;background:var(--line)}
.play{position:absolute;width:28px;height:28px;border-radius:50%;background:#fff}
.play::after{content:"";position:absolute;left:11px;top:8px;border-left:9px solid var(--blue);border-top:6px solid transparent;border-bottom:6px solid transparent}
.dots{position:absolute;display:flex;gap:6px;align-items:center}
.dots span{width:3px;height:3px;border-radius:50%;background:#c7cbd3}
.dots span:first-child{width:14px;border-radius:2px;background:var(--blue)}
.step{position:absolute;width:30px;height:30px;border-radius:50%;border:1.4px solid #9ec3ef;background:#fff}
.step::after{content:"";position:absolute;left:9px;top:9px;width:10px;height:10px;border:1.5px solid var(--blue);border-radius:2px}
.plan-list{list-style:none;font-size:6.8px;line-height:9.6px;color:var(--text)}
.plan-list li{position:relative;padding-left:13px;margin-bottom:9.4px}
.plan-list li::before{content:"";position:absolute;left:0;top:1px;width:8px;height:8px;border-radius:50%;background:var(--blue-bright)}
.foot-h{font:700 7px/10px "Montserrat",sans-serif;color:var(--blue);letter-spacing:.3px}
.foot-links{font-size:6.8px;line-height:20.2px;color:#6d727c}
.contact b{display:block;font:700 7px/10px "Open Sans",sans-serif;color:var(--ink)}
.contact{font-size:6.6px;line-height:9.6px;color:#6d727c}
.cpin{position:absolute;left:0;width:7px;height:7px;border:1.3px solid var(--blue);border-radius:50%}
</style>
</head>
<body>
<div class="stage">

<section class="page page-one">
  <header class="a topbar">
    <div class="a wordmark" style="left:56px;top:12px"><i></i>BrightLane Promo Works</div>
    <div class="pill" style="left:445px;top:11px;width:54px;background:var(--blue);color:#fff">Login</div>
    <div class="pill" style="left:507px;top:11px;width:61px;border:1px solid #cfd6e2;color:var(--blue)">Sign Up</div>
  </header>
  <nav class="a navbar">
    <span class="active" style="left:58px">Home</span>
    <span style="left:103px">Incentives List</span>
    <span style="left:173px">Get Free Samples</span>
    <span style="left:254px">Integrations</span>
    <span style="left:317px">Industries ▾</span>
    <span style="left:433px">Call or Text ▾</span>
    <span style="left:500px">Book a Demo ▾</span>
  </nav>
  <svg class="a" style="left:0;top:62px" width="624" height="290" viewBox="0 0 624 290" aria-hidden="true">
    <defs><linearGradient id="heroA" x1="0" y1="0" x2="1" y2="1"><stop offset="0" stop-color="#2f2db0"/><stop offset="1" stop-color="#1a1870"/></linearGradient></defs>
    <path d="M0,0 H624 V2 C520,150 330,262 0,236 Z" fill="url(#heroA)"/>
    <path d="M0,236 C330,262 520,150 624,2" fill="none" stroke="#1f7ad8" stroke-width="6"/>
    <circle cx="390" cy="80" r="40" fill="#ffffff" opacity=".06"/>
  </svg>
  <h1 class="a h" style="left:57px;top:124px;width:260px;font-size:21px;line-height:28px;color:#fff">2X-5X Your Sales &amp; Leads OVERNIGHT</h1>
  <p class="a" style="left:57px;top:191px;width:240px;font-size:10.4px;line-height:16.5px;color:#e8e9ff">Give a complementary high value incentives as a bonus gift with the purchase of your product or service.</p>
  <div class="btn" style="left:57px;top:257px;width:151px">Sign Up For a 14 Day Risk Free Trial</div>
  <div class="ph" role="img" aria-label="Fanned stack of colourful incentive cards for hotels, fitness, dining and roundtrip airfare" style="left:350px;top:100px;width:170px;height:196px;background:linear-gradient(160deg,#3ec6c9,#f3a431 40%,#e6457b 70%,#f06a2a);transform:rotate(-12deg);border-radius:8px"></div>
  <div class="social" style="left:596px;top:146px"></div>
  <div class="social" style="left:596px;top:176px"></div>
  <div class="social" style="left:596px;top:208px"></div>
  <div class="social" style="left:596px;top:239px"></div>

  <div class="ph" role="img" aria-label="Grid of six printable gift voucher designs over a soft blue circle" style="left:56px;top:374px;width:238px;height:166px;background:radial-gradient(circle at 40% 50%,#cfe1f7 0 55%,transparent 56%),linear-gradient(135deg,#f4d9c4,#e7b07a 40%,#8a4a7a)"></div>
  <div class="stat" style="left:58px;top:554px"><b>16+</b>Years<br>In Business</div>
  <div class="stat" style="left:137px;top:554px"><b>17K+</b>Clients<br>Enrolled</div>
  <div class="stat" style="left:217px;top:554px"><b>11M+</b>Certificates<br>Circulated</div>
  <div class="divider" style="left:62px;top:591px;width:228px"></div>
  <div class="stat" style="left:58px;top:599px"><b>400K</b>Incentives<br>Redeemed</div>
  <div class="stat" style="left:137px;top:599px"><b>$20M+</b>In Savings<br>For Redeemers</div>
  <div class="stat" style="left:217px;top:599px"><b>100's</b>Reviews &amp;<br>Testimonials</div>

  <h2 class="a h" style="left:327px;top:374px;width:240px;font-size:12px;line-height:15px">GIVE AWAY an unlimited amount of complimentary gift vouchers redeemable for:</h2>
  <ul class="a ticklist" style="left:327px;top:430px;width:250px">
    <li><div class="t">Hotel Saving Cards</div><div class="d">Complimentary $100-$500 Hotel Cards</div></li>
    <li><div class="t">Smart Device Certificates</div><div class="d">Complimentary Smart Devices</div></li>
    <li><div class="t">Restaurant Cards</div><div class="d">Complimentary $100-$500 Dining Cards</div></li>
    <li><div class="t">Airfare Vouchers</div><div class="d">Complimentary Roundtrip Airfare</div></li>
    <li><div class="t">Cruise Certificates</div><div class="d">Complimentary Cruise Getaways</div></li>
    <li><div class="t">Resort Certificates</div><div class="d">Complimentary All Inclusive Vacations</div></li>
  </ul>
  <div class="btn" style="left:327px;top:616px;width:151px">Sign Up For a 14 Day Risk Free Trial</div>

  <div class="a" style="left:0;top:672px;width:624px;height:254px;background:var(--section-gray)"></div>
  <h2 class="a h" style="left:57px;top:744px;width:230px;font-size:14px;line-height:18px">THE 4 MAJOR AREAS That Matter Most To Your Business</h2>
  <p class="a" style="left:57px;top:790px;width:220px;font-size:9px;line-height:13.5px">And how using high value incentives seamlessly integrates with them.</p>
  <div class="btn" style="left:57px;top:836px;width:151px">Sign Up For a 14 Day Risk Free Trial</div>
  <div class="ficon" style="left:344px;top:708px"></div>
  <div class="ficon" style="left:408px;top:708px"></div>
  <div class="ficon" style="left:470px;top:708px"></div>
  <div class="ficon" style="left:534px;top:708px"></div>
  <div class="a" style="left:327px;top:736px;width:240px;height:1px;background:var(--line)"></div>
  <div class="a" style="left:327px;top:735px;width:52px;height:2px;background:var(--blue)"></div>
  <h3 class="a h" style="left:327px;top:750px;font-size:11px;color:var(--blue)">More Leads</h3>
  <p class="a p" style="left:327px;top:768px;width:240px">Want to see an explosion in response rates of your existing marketing efforts?</p>
  <p class="a h" style="left:327px;top:801px;font-size:7.4px">Use Case</p>
  <p class="a p" style="left:327px;top:815px;width:242px">Use one (or more) of the incentives that come with your BrightLane package as a simple tagline. For example: "Submit your details today and you will receive a FREE Smartwatch or $100 Dining Card, No Purchase Necessary... just for learning about our company"</p>
  <div class="btn light" style="left:327px;top:871px;width:60px">Read More</div>

  <h2 class="a h center" style="left:147px;top:964px;width:330px;font-size:14px;line-height:18px">DISTRIBUTE Valued Package Incentives<br>Branded With Your Logo</h2>
  <div class="a" style="left:532px;top:986px;width:72px;height:72px;border-radius:50%;background:#e3ecf8"></div>
  <div class="icon" style="left:57px;top:1022px"></div>
  <p class="a feature-title" style="left:57px;top:1048px">Tangible Printable PDF Certificates</p>
  <p class="a p" style="left:57px;top:1062px;width:158px">It does something psychologically when your customers have their certificates in-hand. Print them from your own printer and physically hand them out to your customers or send them out in the mail!</p>
  <div class="icon" style="left:57px;top:1136px"></div>
  <p class="a feature-title" style="left:57px;top:1161px">Send Digital E-Certificates By Email</p>
  <p class="a p" style="left:57px;top:1175px;width:160px">Quickly email your customers individual or multiple e-certificates with just one click from your BrightLane account.</p>
  <div class="ph" role="img" aria-label="Video still of a presenter explaining automation features" style="left:234px;top:1021px;width:334px;height:186px;border-radius:0;background:linear-gradient(135deg,#c9cdd3,#8c8f96 55%,#3a3b40)"></div>
  <div class="play" style="left:387px;top:1100px"></div>
  <p class="a h" style="left:243px;top:1188px;font-size:7.4px;color:#fff">BrightLane's Automation Features In Action</p>
  <div class="icon" style="left:57px;top:1222px"></div>
  <p class="a feature-title" style="left:57px;top:1250px;width:158px">QR Codes, Web Banners, FlowLink and API Integrations</p>
  <p class="a p" style="left:57px;top:1276px;width:158px">Whether you know HTML code or not, with a few clicks of the mouse you can install our easy-to use web banners on your thank you pages or automate your incentive distribution from your own forms with BrightLane's FlowLink App or our User-Friendly In House API integration and use our QR Code feature for any campaign, online and offline.</p>
  <div class="icon" style="left:234px;top:1222px"></div>
  <p class="a feature-title" style="left:234px;top:1254px">SMS Certificates</p>
  <p class="a p" style="left:234px;top:1268px;width:160px">With 98% open rates (compared to 20% with email), you are going to love our SMS feature that allows you to send incentives where your customers are checking 47 times per day – to their phone.</p>
  <div class="icon" style="left:411px;top:1222px"></div>
  <p class="a feature-title" style="left:411px;top:1254px">Eye-Catching Pop-Ups and Sticky Bars</p>
  <p class="a p" style="left:411px;top:1268px;width:160px">Want an influx of high-converting leads? Simply install our attractive and customizable pop-ups and sticky bars on your site and watch your conversions explode! Dana Whitfield reported seeing a 46% increase in sign-ups after implementing pop-up on his personal blog, DanaWhitfield.com (without using high value incentives!). BlogCraft credits its sticky bar with a 25% increase in subscriptions. (imagine adding high value incentives to boot!)</p>
  <div class="btn" style="left:236px;top:1411px;width:152px">Sign Up For a 14 Day Risk Free Trial</div>

  <svg class="a" style="left:0;top:1467px" width="624" height="322" viewBox="0 0 624 322" aria-hidden="true">
    <defs><linearGradient id="giveA" x1="0" y1="0" x2="1" y2="1"><stop offset="0" stop-color="#2f2db0"/><stop offset="1" stop-color="#1b1975"/></linearGradient></defs>
    <path d="M0,0 H624 V322 H330 C220,300 90,262 0,232 Z" fill="url(#giveA)"/>
    <path d="M0,232 C90,262 220,300 330,322" fill="none" stroke="#1f7ad8" stroke-width="6"/>
  </svg>
  <div class="ph" role="img" aria-label="Desktop, tablet and phone screens showing incentive certificate designs" style="left:74px;top:1504px;width:210px;height:200px;background:linear-gradient(145deg,#d9dde6,#7d8aa8 45%,#3a2f6b)"></div>
  <h2 class="a h" style="left:327px;top:1518px;width:240px;font-size:12px;line-height:15.5px;color:#fff">GIVEAWAY unlimited incentives that ranged in retail value of $25-$3,000</h2>
  <ul class="a dotlist" style="left:327px;top:1556px;width:125px">
    <li>Hotel Stays</li><li>Roundtrip Airfare</li><li>7 Night Condo Stays</li><li>Luxury Cruise Getaways</li><li>$100-$500 Dining Cash Cards</li><li>$100-$500 Hotel Savings Cards</li>
  </ul>
  <ul class="a dotlist" style="left:455px;top:1556px;width:125px">
    <li>$100 Wine Vouchers</li><li>Premium Wireless Earbuds</li><li>Smartwatches</li><li>Mexico Beach Vacations</li><li>Portable Bluetooth Speakers</li><li>and much more!</li>
  </ul>
  <div class="btn" style="left:327px;top:1672px;width:151px">Sign Up For a 14 Day Risk Free Trial</div>
</section>

<section class="page page-two">
  <svg class="a" style="left:0;top:0" width="624" height="135" viewBox="0 0 624 135" aria-hidden="true">
    <defs><linearGradient id="giveB" x1="0" y1="0" x2="1" y2="1"><stop offset="0" stop-color="#2c2aaa"/><stop offset="1" stop-color="#1b1975"/></linearGradient></defs>
    <path d="M0,0 H624 V96 C500,132 300,124 60,20 L0,0 Z" fill="url(#giveB)"/>
    <path d="M60,20 C300,124 500,132 624,96" fill="none" stroke="#1f7ad8" stroke-width="6"/>
  </svg>
  <div class="ph" role="img" aria-label="Bottom edge of device screens showing certificate designs" style="left:74px;top:0;width:190px;height:70px;border-radius:0 0 6px 6px;background:linear-gradient(145deg,#c8cdda,#5d5a96 60%,#2b2160)"></div>
  <ul class="a dotlist" style="left:326px;top:-2px;width:120px"><li>$100-$500 Hotel Savings Cards</li></ul>
  <ul class="a dotlist" style="left:454px;top:-2px;width:120px"><li>and much more!</li></ul>
  <div class="btn" style="left:326px;top:40px;width:151px">Sign Up For a 14 Day Risk Free Trial</div>

  <h2 class="a h center" style="left:62px;top:166px;width:500px;font-size:14px;line-height:18px">DONE-FOR-YOU<br>Promotional Marketing Assets Like A Boss!</h2>
  <p class="a center" style="left:132px;top:212px;width:360px;font-size:9px;line-height:13.5px">Imagine having full-colored, professionally designed flyers and posters for each incentive at your disposal...</p>
  <div class="divider" style="left:56px;top:262px;width:512px"></div>

  <div class="ph" role="img" aria-label="Line illustration of people with a phone and megaphone promoting offers" style="left:74px;top:285px;width:195px;height:180px;background:linear-gradient(160deg,#f6f7f9,#e4e7ec)"></div>
  <p class="a h" style="left:326px;top:317px;font-size:8.6px;line-height:14px;color:var(--blue)">Yes, that's right.<br>We're proud to say we got you covered.</p>
  <p class="a p" style="left:326px;top:350px;width:242px">With a few clicks in your BrightLane dashboard, simply send them in their way to your local print shop or print them from yourself and distribute them as you please...</p>
  <p class="a p" style="left:326px;top:390px;width:242px">Wait, you're telling us <b>you want to stand out and capture the attention</b> of your current customer-base so they keep coming back for more... while nudging those leads that haven't pulled the trigger to finally do business with you?</p>
  <div class="divider" style="left:56px;top:487px;width:512px"></div>

  <p class="a h right" style="left:56px;top:534px;width:241px;font-size:8.6px;color:var(--blue)">If you said 'Yes', Woderful...</p>
  <p class="a p right" style="left:56px;top:554px;width:241px">Because - from customer appreciation and warm lead letter templates to <b>impactful professionally created promo videos for every incentive proven to maximize just about any marketing campaign</b>... that and so much more will be readily available to you in your BrightLane dashboard!</p>
  <p class="a p right" style="left:56px;top:616px;width:241px">Combining your experience (with a tip here and there along the way), consider yourself an <b>unstoppable marketing assassin</b> equipped with high-valued incentives to optimize your marketing efforts - and keep your business pumping like a freak train through <b>whatever economic cycle</b>.</p>
  <div class="ph" role="img" aria-label="Line illustration of a person beside a large gift and tablet" style="left:354px;top:510px;width:180px;height:180px;background:linear-gradient(160deg,#f6f7f9,#e4e7ec)"></div>
  <div class="divider" style="left:56px;top:714px;width:512px"></div>

  <div class="icon" style="left:122px;top:747px"></div>
  <p class="a feature-title center" style="left:56px;top:774px;width:148px">Eye-Catching Posters, Flyers &amp; Brochures</p>
  <p class="a p center" style="left:56px;top:799px;width:148px">Professionally made to help you promote the incentives to your audience and designed to maximize offline marketing efforts – at all social events and with every direct mail piece.</p>
  <div class="icon" style="left:303px;top:747px"></div>
  <p class="a feature-title center" style="left:236px;top:774px;width:150px">Professional-Grade Promo Videos For Each Incentive</p>
  <p class="a p center" style="left:236px;top:799px;width:150px">Experiences they'd love to have in movie-like-videos they'll lose themselves in, how can your leads not take you up on your offer?</p>
  <div class="icon" style="left:486px;top:747px"></div>
  <p class="a feature-title center" style="left:419px;top:774px;width:152px">User-Friendly White Label Redemption Site Your Customers Will Love</p>
  <p class="a p center" style="left:419px;top:799px;width:152px">Clean, professional, and simple-to-use. Your customers can redeem their incentive in a matter of seconds with your business happily in mind.</p>
  <div class="btn" style="left:235px;top:885px;width:153px">Sign Up For a 14 Day Risk Free Trial</div>

  <div class="a" style="left:0;top:942px;width:624px;height:333px;background:var(--section-gray)"></div>
  <div class="a" style="left:56px;top:978px;width:511px;height:218px;background:#fff"></div>
  <div class="ph" role="img" aria-label="Photo of two people shaking hands in an office" style="left:56px;top:978px;width:256px;height:218px;border-radius:0;background:linear-gradient(150deg,#56606e,#2b3039 55%,#8d939c)"></div>
  <p class="a h" style="left:74px;top:997px;font-size:14px;color:#fff">Our ALLIANCES</p>
  <p class="a" style="left:74px;top:1166px;font-size:9px;color:#f1f1f1">That help make this possible</p>
  <p class="a h center" style="left:320px;top:1058px;width:240px;font-size:17px;line-height:22px;font-weight:600;color:#2a2a2e">Harborview<br>Residence Club</p>
  <div class="dots" style="left:396px;top:1175px"><span></span><span></span><span></span><span></span><span></span><span></span><span></span><span></span><span></span></div>
  <div class="btn" style="left:235px;top:1219px;width:153px">Sign Up For a 14 Day Risk Free Trial</div>

  <h2 class="a h center" style="left:112px;top:1312px;width:400px;font-size:14px">WORDS From Our Customers</h2>
  <div class="ph" role="img" aria-label="Video testimonial filmed in a recording studio" style="left:166px;top:1352px;width:292px;height:163px;border-radius:0;background:linear-gradient(160deg,#2c5f99,#1c3b66 55%,#6a4a2b)"></div>
  <div class="play" style="left:298px;top:1420px"></div>
  <p class="a center" style="left:176px;top:1489px;width:272px;font-size:9.6px;line-height:12px;color:#fff">Hello, I'm Leon Forbes from Hollywood, Ca. I've been a veteran</p>
  <p class="a h center" style="left:166px;top:1523px;width:292px;font-size:7.4px">Dr. Leon Forbes</p>
  <div class="a" style="left:57px;top:1435px;width:16px;height:16px;border-radius:50%;border:1px solid #b8c4d6;font:9px/14px sans-serif;color:var(--blue);text-align:center">←</div>
  <p class="a h" style="left:84px;top:1439px;font-size:7.4px">Marcus Lane</p>
  <p class="a h right" style="left:470px;top:1433px;width:70px;font-size:7.4px;line-height:10px">Renee<br>Calder</p>
  <div class="a" style="left:551px;top:1435px;width:16px;height:16px;border-radius:50%;border:1px solid #b8c4d6;font:9px/14px sans-serif;color:var(--blue);text-align:center">→</div>
  <div class="btn" style="left:235px;top:1557px;width:153px">Sign Up For a 14 Day Risk Free Trial</div>

  <svg class="a" style="left:0;top:1596px" width="624" height="229" viewBox="0 0 624 229" aria-hidden="true">
    <defs><linearGradient id="tooA" x1="0" y1="0" x2="1" y2="1"><stop offset="0" stop-color="#2c2aaa"/><stop offset="1" stop-color="#1b1975"/></linearGradient></defs>
    <path d="M0,70 C220,14 420,2 624,0 V229 H0 Z" fill="url(#tooA)"/>
    <path d="M0,70 C220,14 420,2 624,0" fill="none" stroke="#1f7ad8" stroke-width="6"/>
  </svg>
  <h2 class="a h" style="left:56px;top:1686px;font-size:12px;color:#fff">Sounds TOO GOOD TO BE TRUE?</h2>
  <ul class="a bullets" style="left:56px;top:1712px;width:322px">
    <li>It's very important for you to understand how we are able to do this. First off, hotels and resorts are rarely full but they are always open and still have their fixed costs and always have unused rooms available.</li>
    <li>So what they do is partner up with marketing companies like us to help them fill up their otherwise empty rooms that they end up turning into additional revenue from other parts of their property like their in-house restaurants, the bar, the casino, room service, the spa or even an extra day stay.</li>
    <li>They're actually doing it for some of the same reasons why you would be using our certificates, to increase their repeat and referral business.</li>
  </ul>
  <div class="ph" role="img" aria-label="Circular video still of a presenter in a suit" style="left:404px;top:1650px;width:165px;height:190px;border-radius:50%;background:radial-gradient(circle at 50% 35%,#c9d8ea,#7b94b5 55%,#2a2d3a)"></div>
  <div class="play" style="left:472px;top:1770px"></div>
</section>

<section class="page page-three">
  <div class="a" style="left:0;top:0;width:624px;height:272px;background:linear-gradient(135deg,#2c2aaa,#1b1975)"></div>
  <svg class="a" style="left:420px;top:150px" width="204" height="122" viewBox="0 0 204 122" aria-hidden="true">
    <path d="M0,122 C90,110 170,70 204,0 V122 Z" fill="#1f7ad8" opacity=".9"/>
  </svg>
  <h2 class="a h" style="left:56px;top:19px;font-size:12px;color:#fff">Sounds TOO GOOD TO BE TRUE?</h2>
  <ul class="a bullets" style="left:56px;top:45px;width:322px">
    <li>It's very important for you to understand how we are able to do this. First off, hotels and resorts are rarely full but they are always open and still have their fixed costs and always have unused rooms available.</li>
    <li>So what they do is partner up with marketing companies like us to help them fill up their otherwise empty rooms that they end up turning into additional revenue from other parts of their property like their in-house restaurants, the bar, the casino, room service, the spa or even an extra day stay.</li>
    <li>They're actually doing it for some of the same reasons why you would be using our certificates, to increase their repeat and referral business.</li>
    <li>They know that if they show your customers a good time while they're there, they'll be more likely to tell their friends and family about the great time they had and will be more likely to book with the property in the future as a regular paying customer.</li>
  </ul>
  <div class="btn" style="left:56px;top:217px;width:152px">Sign Up For a 14 Day Risk Free Trial</div>
  <div class="ph" role="img" aria-label="Circular video still of a presenter in a suit" style="left:404px;top:34px;width:163px;height:163px;border-radius:50%;background:radial-gradient(circle at 50% 35%,#d3e1f0,#7b94b5 55%,#2a2d3a)"></div>
  <div class="play" style="left:471px;top:102px"></div>
  <p class="a h" style="left:405px;top:211px;font-size:6.8px;color:#fff">Watch Video On 'How Can We Do It?'</p>

  <div class="a" style="left:0;top:272px;width:624px;height:334px;background:var(--section-gray)"></div>
  <div class="a" style="left:56px;top:310px;width:511px;height:217px;background:#fff"></div>
  <div class="ph" role="img" aria-label="Upward view of glass skyscrapers" style="left:56px;top:310px;width:256px;height:217px;border-radius:0;background:linear-gradient(170deg,#c5ccd6,#7c8795 50%,#4b5563)"></div>
  <p class="a h" style="left:74px;top:329px;font-size:14px;color:#fff">Our CLIENTS</p>
  <p class="a" style="left:74px;top:484px;width:220px;font-size:9px;line-height:13px;color:#fff">A few of our clients that giveaway thousands of incentives each and every month</p>
  <p class="a h center" style="left:320px;top:422px;width:240px;font-size:14px;font-weight:800;color:#1c1c22">NORTHWIND PLANS</p>
  <div class="dots" style="left:392px;top:507px"><span></span><span></span><span></span><span></span><span></span><span></span><span></span><span></span><span></span><span></span></div>
  <div class="btn" style="left:235px;top:551px;width:153px">Sign Up For a 14 Day Risk Free Trial</div>

  <h2 class="a h" style="left:56px;top:644px;font-size:15px">RISK FREE Tial</h2>
  <p class="a h" style="left:56px;top:670px;font-size:9px;color:var(--blue)">14 Days Money Back Guarantee</p>
  <p class="a p" style="left:56px;top:690px;width:236px">With access to over 30 different incentives in 6 different categories that you get to test offers with it is impossible to effectively test the BrightLane platform in under 14 days.</p>
  <p class="a p" style="left:56px;top:731px;width:236px">But we are willing to put our money where our mouth is. If you contact us and let us know that you simply made a mistake signing up for our service and as long as you meet all three requirements below we might just refund you in full.</p>
  <div class="a" style="left:340px;top:660px;width:1px;height:100px;background:#cfe0f3"></div>
  <div class="step" style="left:326px;top:643px"></div>
  <p class="a p" style="left:368px;top:648px;width:200px"><b>Login</b> to your account and hit the cancel button (pretty basic stuff guys)</p>
  <div class="step" style="left:326px;top:693px"></div>
  <p class="a p" style="left:368px;top:692px;width:200px">Request a refund within 14 days by clicking on the <b>support button</b> on every page of this website (with your lame and boring reasoning)</p>
  <div class="step" style="left:326px;top:743px"></div>
  <p class="a p" style="left:368px;top:753px;width:200px">Patiently <b>wait</b> for your refund to be processed (yawn...)</p>
  <div class="ph" role="img" aria-label="Handwritten owner signature" style="left:270px;top:800px;width:84px;height:48px;background:linear-gradient(135deg,#f4f5f7,#e5e7eb)"></div>
  <div class="btn" style="left:235px;top:872px;width:153px">Sign Up For a 14 Day Risk Free Trial</div>

  <svg class="a" style="left:0;top:952px" width="624" height="404" viewBox="0 0 624 404" aria-hidden="true">
    <defs><linearGradient id="planA" x1="0" y1="0" x2="1" y2="1"><stop offset="0" stop-color="#2c2aaa"/><stop offset="1" stop-color="#1b1975"/></linearGradient></defs>
    <path d="M0,98 C150,40 400,6 624,2 V404 H0 Z" fill="url(#planA)"/>
    <path d="M0,98 C150,40 400,6 624,2" fill="none" stroke="#1f7ad8" stroke-width="7"/>
  </svg>
  <h2 class="a h right" style="left:300px;top:972px;width:267px;font-size:15px;color:#fff">Choose Your PLAN</h2>
  <p class="a right" style="left:300px;top:995px;width:267px;font-size:8.6px;color:#e3e5ff">(Each Plan Has A $199 Set Up Fee)</p>
  <div class="a" style="left:56px;top:1030px;width:511px;height:248px;background:#fff;border-radius:3px"></div>
  <p class="a h" style="left:251px;top:1043px;font-size:8.4px;color:var(--blue)">Monthly</p>
  <div class="a" style="left:234px;top:1064px;width:74px;height:2px;background:var(--blue)"></div>
  <div class="a" style="left:56px;top:1065px;width:511px;height:1px;background:var(--line)"></div>
  <p class="a h" style="left:337px;top:1043px;font-size:8.4px;color:#333">Annual</p>
  <div class="ph" role="img" aria-label="Dark office photo background behind the plan price" style="left:71px;top:1080px;width:136px;height:182px;border-radius:0;background:linear-gradient(165deg,#33363e,#15171c 60%,#3e4652)"></div>
  <p class="a h center" style="left:71px;top:1095px;width:136px;font-size:11.5px;line-height:15px;color:#fff">Unlimited<br>MONTHLY</p>
  <p class="a h center" style="left:71px;top:1154px;width:136px;font-size:20px;color:#fff">$99</p>
  <p class="a center" style="left:71px;top:1184px;width:136px;font-size:8px;color:#ddd">/ month</p>
  <p class="a h center" style="left:79px;top:1226px;width:120px;font-size:6.6px;line-height:10px;color:#fff">$298 today <span style="font-weight:500">then only</span> $99 per month <span style="font-weight:500">thereafter</span></p>
  <ul class="a plan-list" style="left:222px;top:1081px;width:155px">
    <li>One account can be used for unlimited brands (great for agencies)</li>
    <li>Unlimited access to all our incentives in 6 categories</li>
    <li>Send unlimited incentives from your own business email</li>
    <li>Send unlimited incentives by SMS / text messages</li>
    <li>Automate sending unlimited incentives via landing pages</li>
    <li>Automate sending unlimited incentives via website sticky bars</li>
  </ul>
  <ul class="a plan-list" style="left:394px;top:1081px;width:160px">
    <li>Automate sending unlimited incentives via website popups</li>
    <li>Automate sending unlimited incentives via our API</li>
    <li>Automate sending unlimited incentives via QR codes</li>
    <li>Automate sending unlimited incentives via our FlowLink App integration</li>
    <li>Eye-catching promo videos, posters and flyers to help you promote the incentives to your audience</li>
    <li>50% commission affiliate program (white label included)</li>
  </ul>
  <div class="btn" style="left:235px;top:1289px;width:153px">Sign Up For a 14 Day Risk Free Trial</div>

  <footer>
    <div class="a" style="left:0;top:1356px;width:624px;height:404px;background:linear-gradient(180deg,#f7f8fa,#eef0f3)"></div>
    <div class="a wordmark center" style="left:0;top:1390px;width:624px">BrightLane Promo Works</div>
    <p class="a foot-h" style="left:56px;top:1438px">CONTACT US</p>
    <div class="a contact" style="left:56px;top:1465px;width:190px">
      <span class="cpin" style="top:2px"></span>
      <div style="padding-left:15px"><b>BrightLane Promo Works Group, Inc.</b>2410 Harbor Crest Rd #220<br>Seaview, CA 90000</div>
      <span class="cpin" style="top:44px"></span>
      <div style="padding-left:15px;margin-top:12px"><b>Book a Demo</b>• New Sales<br>• Current/Past Clients</div>
      <span class="cpin" style="top:87px"></span>
      <div style="padding-left:15px;margin-top:12px"><b>Call or Text Us</b>• New Sales : 1-555-210-4180<br>• Current/Past Clients : 1-555-310-7725</div>
      <span class="cpin" style="top:129px"></span>
      <div style="padding-left:15px;margin-top:12px"><b>Email Us</b>support@brightlanepromoworks.biz</div>
      <span class="cpin" style="top:161px"></span>
      <div style="padding-left:15px;margin-top:12px"><b>Online Support</b>• Monday - Friday 8am | 5pm PST<br>• Sat/Sun/Holidays : <span style="color:#e23b3b">Closed</span><br>• After hours all inquiries will be replied to on the next business day</div>
    </div>
    <p class="a foot-h" style="left:275px;top:1438px">QUICK LINKS</p>
    <div class="a foot-links" style="left:275px;top:1462px;width:120px">Home<br>The Incentives<br>Login<br>Sign Up<br>Affiliate<br>Integrations<br>Testimonials<br>Frequently Asked Questions<br><span style="display:block;line-height:10px;margin:5px 0">BrightLane Distribute Certificate Demo Videos</span>White Label Agency Program</div>
    <p class="a foot-h" style="left:440px;top:1438px">OTHER LINKS</p>
    <div class="a foot-links" style="left:440px;top:1462px;width:128px">Hoteliers<br>BrightLane Certificates List<br>How To Use BrightLane Certificates<br>Pop Ups &amp; Sticky Bars<br>Whitepaper - Increase Sales<br><span style="display:block;line-height:10px;margin:5px 0">Whitepaper - Improve Sales During Strange Times</span><span style="display:block;line-height:10px;margin:10px 0 0">Whitepaper - Boost Website Conversions</span></div>
    <div class="btn" style="left:235px;top:1708px;width:153px">Sign Up For a 14 Day Risk Free Trial</div>
    <div class="a" style="left:0;top:1760px;width:624px;height:28px;background:#fff;border-top:1px solid var(--line)"></div>
    <p class="a" style="left:56px;top:1769px;font-size:6.2px;color:#6d727c">© 2024 BrightLane Promo Works Group, Inc. All Rights Reserved. &nbsp;&nbsp;|&nbsp;&nbsp; Privacy Policy &nbsp;&nbsp;|&nbsp;&nbsp; Terms &amp; Conditions</p>
    <div class="a" style="left:490px;top:1769px;width:9px;height:9px;border-radius:50%;background:#2a2a2e"></div>
    <div class="a" style="left:510px;top:1769px;width:9px;height:9px;border-radius:50%;background:#2a2a2e"></div>
    <div class="a" style="left:530px;top:1769px;width:9px;height:9px;border-radius:50%;background:#2a2a2e"></div>
    <div class="a" style="left:550px;top:1769px;width:9px;height:9px;border-radius:50%;background:#2a2a2e"></div>
    <div class="a h" style="left:566px;top:1768px;width:58px;height:20px;background:#fff;box-shadow:0 1px 4px rgba(0,0,0,.2);border-radius:3px 0 0 0;font-size:7px;line-height:20px;text-align:center;color:var(--blue)">● Support</div>
  </footer>
</section>

</div>
</body>
</html>
```